Local Flower Farm Needs Business Card Design

I need business cards designed for a flower farm based in Eudora, Kansas.
Business Info:
We are a local cut flower farm located in Eudora, Kansas, founded by Corinne Haldwick. What started as a passion for agriculture and search for more joy in daily life has blossomed into a small business dedicated to providing the community with beautiful, fresh, and sustainable flowers. We specialize in local, seasonal blooms, ensuring that every petal reflects the care and dedication we pour into our craft. Our mission is to deliver the highest quality flowers directly to our customers through local farmers markets and to florists who share our commitment to sustainability. Join us in celebrating the beauty of nature, one bloom at a time!
Contact Details:
Corinne Haldwick
Owner
Phone 913-555-0147
Facebook: Rosalind Thorpe Gardens
Instagram: @RosalindThorpeGardens
Website: RosalindThorpeGardens.example
Target Market(s)
Wholesale to Florists and Direct to Consumer via Farmers Market
Industry/Entity Type
Florist, Farm
Contact Information for Business Card
Name, Contact Info, Logo
Look and feel
Each slider illustrates characteristics of the customer's brand and the style your logo design should communicate.

```html
<!DOCTYPE html>
<html lang="en">
<head>
<meta charset="utf-8">
<title>Rosalind Thorpe Gardens — Business Card</title>
<link href="https://fonts.googleapis.com/css2?family=Arimo:wght@400;700&display=swap" rel="stylesheet">
<style>
  :root {
    --ink: #0d2a2e;
    --paper: #ffffff;
    --stage: #2a2a2a;
    --muted: #e8eeee;
  }
  * { margin: 0; padding: 0; box-sizing: border-box; }
  html, body { width: 1200px; height: 900px; overflow: hidden; background: var(--stage); }
  body { position: relative; font-family: "Arimo", Arial, sans-serif; }

  .card {
    position: absolute;
    width: 600px;
    height: 343px;
    border-radius: 22px;
    overflow: hidden;
  }

  /* Back of card */
  .card-back { left: 60px; top: 90px; background: var(--ink); }
  .back-seal {
    position: absolute;
    left: 50%; top: 46%;
    width: 200px; height: 200px;
    transform: translate(-50%, -50%);
    border: 1.5px solid var(--paper);
    border-radius: 50%;
    display: flex; align-items: center; justify-content: center;
    text-align: center;
  }
  .seal-name {
    font-weight: 400;
    font-size: 19px;
    line-height: 1.35;
    letter-spacing: 2px;
    text-transform: uppercase;
  }
  .back-seal .seal-name { color: var(--paper); }

  /* Front of card */
  .card-front { left: 540px; top: 467px; background: var(--paper); }
  .front-band {
    position: absolute;
    left: 0; right: 0;
    top: 62px; height: 210px;
    background: var(--ink);
  }
  .front-seal {
    position: absolute;
    left: 360px; top: 50px;
    width: 220px; height: 220px;
    border-radius: 50%;
    background: var(--paper);
    display: flex; align-items: center; justify-content: center;
  }
  .front-seal-ring {
    width: 192px; height: 192px;
    border: 1.5px solid var(--ink);
    border-radius: 50%;
    display: flex; align-items: center; justify-content: center;
    text-align: center;
  }
  .front-seal .seal-name { color: var(--ink); }

  .contact-block {
    position: absolute;
    left: 34px; top: 118px;
    color: var(--paper);
  }
  .person-name {
    font-weight: 700;
    font-size: 22px;
    letter-spacing: 0.5px;
    text-transform: uppercase;
  }
  .person-role { font-size: 13px; margin-top: 2px; }
  .divider { width: 12px; height: 1px; background: var(--paper); margin: 10px 0 8px; }
  .contact-list { list-style: none; }
  .contact-list li {
    display: flex; align-items: center; gap: 8px;
    font-size: 14px; line-height: 21px;
  }
  .contact-icon { width: 11px; height: 11px; flex: none; }
</style>
</head>
<body>

  <section class="card card-back" aria-label="Card back">
    <div class="back-seal">
      <span class="seal-name">Rosalind<br>Thorpe<br>Gardens</span>
    </div>
  </section>

  <section class="card card-front" aria-label="Card front">
    <div class="front-band"></div>

    <div class="front-seal">
      <div class="front-seal-ring">
        <span class="seal-name">Rosalind<br>Thorpe<br>Gardens</span>
      </div>
    </div>

    <div class="contact-block">
      <h1 class="person-name">Corinne Haldwick</h1>
      <p class="person-role">Owner</p>
      <div class="divider"></div>
      <ul class="contact-list">
        <li>
          <svg class="contact-icon" viewBox="0 0 24 24" aria-hidden="true"><path fill="#fff" d="M6.6 10.8a15.2 15.2 0 0 0 6.6 6.6l2.2-2.2a1 1 0 0 1 1-.25 11.4 11.4 0 0 0 3.6.57 1 1 0 0 1 1 1V20a1 1 0 0 1-1 1A17 17 0 0 1 3 4a1 1 0 0 1 1-1h3.5a1 1 0 0 1 1 1c0 1.25.2 2.45.57 3.57a1 1 0 0 1-.25 1z"/></svg>
          913-555-0147
        </li>
        <li>
          <svg class="contact-icon" viewBox="0 0 12 12" aria-hidden="true"><circle cx="6" cy="6" r="5.5" fill="#fff"/></svg>
          Rosalind Thorpe Gardens
        </li>
        <li>
          <svg class="contact-icon" viewBox="0 0 12 12" aria-hidden="true"><circle cx="6" cy="6" r="5.5" fill="#fff"/></svg>
          @RosalindThorpeGardens
        </li>
        <li>
          <svg class="contact-icon" viewBox="0 0 12 12" aria-hidden="true"><circle cx="6" cy="6" r="5.5" fill="#fff"/></svg>
          RosalindThorpeGardens.example
        </li>
      </ul>
    </div>
  </section>

</body>
</html>
```